Varentoria Business Card and Letter Head

We are a leadership assessment consultancy based in Sydney, Australia. We help executive-level decison-makers select leaders for more senior level roles in corporate and government organisations. Our methodology is based on the latest research from the field of neuroscience.
We need a business card design and matching letter head that presents our company, Varentoria, as a:
1. trusted adviser to senior executive-level decison makers
2. niche consultancy who are experts in the field of assessing leadership talent
3. results-focused solution provider who balance scientific methods with pragmatic solutions
The following company details should be used in all designs:
Company Name: Varentoria
Details (for business card):
Derek Hanford
Prime Capacity Officer
Level 29, Marlow Tower
7 Marlow Square
Sydney, NSW 2000 Australia
Phone: 1300 582 714
Mobile: 0412 637 258
Email: derek.hanford@varentoria-example.com.au
Website: varentoria-example.com.au
I have attached the logo for Varentoria (for both a white and black background) - your business card and letter head designs must incoporate this logo and colour scheme.
Thanks for your interest in this project, I'm looking forward to receiving your ideas.
Regards,
Derek
Target Market(s)
Executive-level decison-makers in corporate and government organisations (e.g., CEO, VP, Head of Human Resources)
Industry/Entity Type
Leadership
Look and feel

```html
<!DOCTYPE html>
<html lang="en">
<head>
<meta charset="utf-8">
<title>Varentoria Business Card</title>
<link href="https://fonts.googleapis.com/css2?family=Open+Sans:wght@300;400;600;700&display=swap" rel="stylesheet">
<style>
  :root {
    --backdrop: #6b4a33;
    --card-white: #ffffff;
    --brand-red: #d8151f;
    --brand-red-dark: #a50f16;
    --brand-red-light: #ee2a33;
    --maroon: #3b0a0d;
    --charcoal: #3d3d3f;
    --text-grey: #333333;
    --tag-grey: #555555;
  }
  * { margin: 0; padding: 0; box-sizing: border-box; }
  html, body { width: 1200px; height: 427px; overflow: hidden; }
  body {
    background: var(--backdrop);
    font-family: "Open Sans", Arial, sans-serif;
    position: relative;
  }
  .card {
    position: absolute;
    top: 50px;
    width: 519px;
    height: 297px;
    border-radius: 20px;
    overflow: hidden;
    box-shadow: 0 6px 14px rgba(0,0,0,0.35);
  }
  .card-front { left: 63px; background: var(--card-white); }
  .card-back {
    left: 613px;
    background: linear-gradient(90deg, var(--brand-red-dark) 0%, var(--brand-red) 45%, var(--brand-red-light) 100%);
  }
  .card-shapes { position: absolute; inset: 0; }
  .brand-name {
    position: absolute;
    left: 27px; top: 30px;
    font-size: 44px;
    font-weight: 600;
    color: var(--charcoal);
    letter-spacing: -0.5px;
    line-height: 1;
  }
  .tagline {
    position: absolute;
    left: 29px; top: 86px;
    font-size: 14.5px;
    font-weight: 300;
    color: var(--tag-grey);
    letter-spacing: 0.6px;
    white-space: nowrap;
  }
  .person-name {
    position: absolute;
    left: 27px; top: 150px;
    font-size: 18px;
    font-weight: 700;
    color: var(--brand-red-dark);
  }
  .person-title {
    position: absolute;
    left: 27px; top: 174px;
    font-size: 12.5px;
    color: var(--text-grey);
  }
  .website {
    position: absolute;
    left: 230px; top: 158px;
    font-size: 9.5px;
    font-weight: 700;
    color: var(--text-grey);
    white-space: nowrap;
  }
  .address, .contacts {
    position: absolute;
    top: 221px;
    font-size: 12px;
    line-height: 16.5px;
    color: var(--text-grey);
    white-space: nowrap;
  }
  .address { left: 27px; }
  .contacts { left: 230px; }
  .contacts .label { color: var(--brand-red); }
  .back-name {
    position: absolute;
    right: 30px; top: 110px;
    font-size: 34px;
    font-weight: 600;
    color: var(--maroon);
  }
  .back-url {
    position: absolute;
    left: 160px; top: 172px;
    font-size: 11px;
    color: #ffffff;
    letter-spacing: 1.5px;
    white-space: nowrap;
  }
</style>
</head>
<body>
  <section class="card card-front">
    <svg class="card-shapes" width="519" height="297" viewBox="0 0 519 297">
      <defs>
        <linearGradient id="foldRed" x1="0" y1="0" x2="1" y2="1">
          <stop offset="0" stop-color="#ee2a33"/>
          <stop offset="1" stop-color="#a50f16"/>
        </linearGradient>
      </defs>
      <polygon points="445,0 519,0 519,42 405,168 478,55 445,55" fill="url(#foldRed)"/>
      <rect x="0" y="178" width="10" height="119" fill="#3d3d3f"/>
      <rect x="0" y="288" width="109" height="9" fill="#2a2a2b"/>
    </svg>
    <div class="brand-name">Varentoria</div>
    <div class="tagline">ASSESSING LEADERSHIP STRENGTH</div>
    <div class="person-name">Derek Hanford</div>
    <div class="person-title">Prime Capacity Officer</div>
    <div class="website">www.VARENTORIA-EXAMPLE.com.au</div>
    <div class="address">
      Level 29, Marlow Tower<br>
      7 Marlow Square, Sydney,<br>
      NSW 2000 Australia
    </div>
    <div class="contacts">
      <span class="label">P:</span> 1300 582 714<br>
      <span class="label">M:</span> 0412 637 258<br>
      <span class="label">E:</span> derek.hanford@varentoria-example.com.au
    </div>
  </section>

  <section class="card card-back">
    <svg class="card-shapes" width="519" height="297" viewBox="0 0 519 297">
      <defs>
        <linearGradient id="backFold" x1="0" y1="0" x2="1" y2="1">
          <stop offset="0" stop-color="#f03a42"/>
          <stop offset="1" stop-color="#b8121a"/>
        </linearGradient>
      </defs>
      <polygon points="0,30 38,42 114,170 0,118" fill="url(#backFold)"/>
      <rect x="410" y="288" width="109" height="9" fill="#8e0d13"/>
    </svg>
    <div class="back-name">Varentoria</div>
    <div class="back-url">VARENTORIA-EXAMPLE . COM . AU</div>
  </section>
</body>
</html>
```